Business Cards Design for the electrical wholesaler: clean bold dynamic :)

We need a business card design that would follow our latest brand guidelines. As an electrical wholesaler we want to bring a fresh look and feel into the industry. The design should be clean bold and dynamic. It should come alive with the renewed energy of our green colour. Our grey colour should keep things balanced and complement the notion of maturity and responsibility. We employ Lato as a corporate font however are not bound by this font and we’re open to interpretation here.

Target Market(s)

Electrical contractors

Industry/Entity Type

Business

Contact Information for Business Card

Logo
Name & Surname: Halyna Dorosh
Job Title: Director of Marketing
Email: halya.dorosh@quillmail.example
Cell phone: XXX.XXX.XXXX
Address: 20517 - 87 Ave. Edmonton, AB, Canada. T6K 4N8
Business Phone: 780.555.0184
Website: www.brovix.example

Font styles to use
Other font styles liked:
• Lato

Requirements
Must have
• Logo & website
Nice to have
• Brand elements - some of them you may find in the attached Brand Guidelines (e.g. three lines on the background signifying "W")

```html
<!DOCTYPE html>
<html lang="en">
<head>
<meta charset="utf-8">
<title>brovix business card</title>
<link rel="stylesheet" href="https://fonts.googleapis.com/css2?family=Work+Sans:wght@400;500&display=swap">
<style>
  :root {
    --stage: #1b1b1b;
    --card-light: #ffffff;
    --card-dark-a: #1a1a1a;
    --card-dark-b: #343434;
    --green: #7dc142;
    --grey: #4b4b4b;
    --grey-soft: #5a5a5a;
    --grey-light: #c4c4c4;
  }
  * { margin: 0; padding: 0; box-sizing: border-box; }
  html, body { width: 1200px; height: 897px; overflow: hidden; }
  body {
    background: var(--stage);
    position: relative;
    font-family: "Work Sans", Arial, sans-serif;
  }
  .card {
    position: absolute;
    left: 303px;
    width: 595px;
    height: 338px;
    border-radius: 22px;
    overflow: hidden;
  }
  .card-front { top: 92px; background: var(--card-light); }
  .card-back {
    top: 469px;
    background: linear-gradient(135deg, var(--card-dark-a) 35%, var(--card-dark-b) 100%);
  }

  .brand {
    position: absolute;
    display: flex;
    align-items: center;
    font-weight: 500;
    letter-spacing: -0.5px;
    line-height: 1;
  }
  .brand-mark { border-radius: 50%; flex: none; }
  .card-front .brand { left: 44px; top: 140px; font-size: 54px; color: var(--grey); gap: 12px; }
  .card-front .brand-mark { width: 40px; height: 40px; background: var(--green); }
  .card-back .brand { left: 0; right: 0; top: 128px; justify-content: center; font-size: 82px; color: var(--grey-light); gap: 18px; }
  .card-back .brand-mark { width: 58px; height: 58px; background: #2a2a2a; box-shadow: inset 0 0 0 1px #3c3c3c; }

  .divider {
    position: absolute;
    left: 313px;
    top: 94px;
    width: 2px;
    height: 150px;
    background: var(--green);
  }
  .contact {
    position: absolute;
    left: 343px;
    top: 91px;
    color: var(--grey-soft);
    font-size: 15px;
    letter-spacing: 0.6px;
  }
  .contact-name { color: var(--green); font-size: 24px; font-weight: 500; letter-spacing: 0.3px; line-height: 1; }
  .contact-title { margin-top: 5px; line-height: 1; }
  .contact-address { margin-top: 12px; line-height: 18.5px; }
  .contact-list { list-style: none; margin-top: 8px; line-height: 19px; }
  .contact-list li { display: flex; align-items: center; gap: 11px; }
  .contact-list svg { width: 9px; height: 9px; flex: none; }
  .accent { color: var(--green); }
</style>
</head>
<body>
  <section class="card card-front">
    <div class="brand"><span class="brand-mark"></span>brovix</div>
    <div class="divider"></div>
    <div class="contact">
      <p class="contact-name">Halyna Dorosh</p>
      <p class="contact-title">Founder</p>
      <p class="contact-address">20517 87ave<br>T6K4N8 Edmonton, Alberta</p>
      <ul class="contact-list">
        <li>
          <svg viewBox="0 0 10 10" aria-hidden="true"><path d="M2 0.5 L3.6 0.5 L4 3 L3 3.8 Q4 6 6.2 7 L7 6 L9.5 6.4 L9.5 8 Q9.5 9.5 8 9.5 Q1 9 0.5 2 Q0.5 0.5 2 0.5Z" fill="var(--green)"/></svg>
          780.555.0184
        </li>
        <li>
          <svg viewBox="0 0 10 10" aria-hidden="true"><rect x="0.7" y="2" width="8.6" height="6.2" fill="none" stroke="var(--green)" stroke-width="1.2"/><path d="M0.9 2.3 L5 5.5 L9.1 2.3" fill="none" stroke="var(--green)" stroke-width="1.2"/></svg>
          hello@brovix.example
        </li>
        <li>
          <svg viewBox="0 0 10 10" aria-hidden="true"><circle cx="5" cy="5" r="4.3" fill="none" stroke="var(--green)" stroke-width="1"/><ellipse cx="5" cy="5" rx="1.9" ry="4.3" fill="none" stroke="var(--green)" stroke-width="0.9"/><path d="M0.7 5 H9.3 M1.5 2.8 H8.5 M1.5 7.2 H8.5" stroke="var(--green)" stroke-width="0.8"/></svg>
          <span>www.<span class="accent">brovix</span>.example</span>
        </li>
      </ul>
    </div>
  </section>

  <section class="card card-back">
    <div class="brand"><span class="brand-mark"></span>brovix</div>
  </section>
</body>
</html>
```